Maple Grove Youngsters Guild Business Card Project

We are a Minneapolis based discount club that caters to families with children. We need a business card that can be used to communicate our contact information to other businesses that may wish to offer discounts on our website.

Please use placeholders for contact information (i.e. John Doe, 123 Any Street, Any Town, etc.) and include spaces for the following: Full name, title, email, phone number, website, one line street address, city, state, and zip code.
Updates

Project Deadline Extended
Reason: I have extended the deadline because I had not intended the project to close so quickly.

Target Market(s)

Most of the time the business cards will be used in business to business situations. However, from time to time they may be distributed to our end customer, families with children.

Industry/Entity Type

Club

Font styles to use
Serif
Sans Serif
Other font styles liked:
• Open to suggestions

Requirements
Nice to have
• We might use the reverse side of the card as the design for our membership card.

```html
<!DOCTYPE html>
<html lang="en">
<head>
<meta charset="utf-8">
<title>Maple Grove Youngsters Guild – Business Card</title>
<link rel="stylesheet" href="https://fonts.googleapis.com/css2?family=Roboto:wght@400;700&display=swap">
<style>
  :root {
    --page-bg: #111214;
    --card-paper: #fbfbf8;
    --wash-blue: #8cc8e6;
    --wash-green: #c9ec9f;
    --wash-red: #e2343a;
    --name-red: #c8262b;
    --ink: #2a2a3a;
    --brand-navy: #1f3f8f;
    --rule: #c9ccd2;
  }
  html, body {
    margin: 0;
    width: 1200px;
    height: 873px;
    overflow: hidden;
    background: var(--page-bg);
    font-family: "Roboto", Arial, sans-serif;
  }
  .sheet {
    position: relative;
    width: 1200px;
    height: 873px;
  }
  .card {
    position: absolute;
    top: 282px;
    width: 540px;
    height: 309px;
    background: var(--card-paper);
    overflow: hidden;
    box-shadow: 0 6px 18px rgba(0,0,0,.5);
  }
  .card--front { left: 40px; }
  .card--back  { left: 620px; }

  .wash {
    position: absolute;
    inset: 0;
    background:
      radial-gradient(ellipse 44% 42% at 14% 16%, var(--wash-blue) 0%, rgba(140,200,230,.55) 45%, rgba(140,200,230,0) 75%),
      radial-gradient(ellipse 48% 46% at 30% 92%, var(--wash-green) 0%, rgba(201,236,159,.6) 50%, rgba(201,236,159,0) 80%),
      radial-gradient(ellipse 30% 70% at 100% 60%, var(--wash-red) 0%, rgba(226,52,58,.75) 40%, rgba(226,52,58,0) 78%);
  }

  .contact {
    position: absolute;
    left: 30px;
    top: 24px;
    color: var(--ink);
  }
  .contact__name {
    margin: 0;
    font-size: 25px;
    font-weight: 400;
    line-height: 1.2;
    color: var(--name-red);
  }
  .contact__title {
    margin: 2px 0 12px;
    font-size: 12px;
  }
  .contact__list {
    list-style: none;
    margin: 0;
    padding: 0;
    font-size: 12px;
  }
  .contact__item {
    display: flex;
    align-items: center;
    gap: 8px;
    height: 19px;
  }
  .contact__icon {
    width: 14px;
    height: 14px;
    flex: none;
  }
  .contact__rule {
    position: absolute;
    left: 30px;
    top: 252px;
    width: 200px;
    border-top: 1px solid var(--rule);
  }

  .brand {
    position: absolute;
    display: flex;
    align-items: center;
    gap: 8px;
    color: var(--brand-navy);
    font-weight: 700;
    line-height: 1.05;
    text-transform: uppercase;
  }
  .brand__dot {
    flex: none;
    border-radius: 50%;
    background: var(--brand-navy);
  }
  .card--front .brand {
    right: 92px;
    bottom: 42px;
    width: 190px;
    font-size: 21px;
  }
  .card--front .brand__dot { width: 16px; height: 16px; }
  .card--back .brand {
    left: 150px;
    top: 96px;
    width: 260px;
    font-size: 31px;
  }
  .card--back .brand__dot { width: 22px; height: 22px; }
</style>
</head>
<body>
<main class="sheet">

  <section class="card card--front" aria-label="Business card, contact side">
    <div class="wash" role="img" aria-label="Soft watercolour washes in blue, green and red"></div>

    <div class="contact">
      <h1 class="contact__name">Dana Whitfield</h1>
      <p class="contact__title">Financial Advisor</p>
      <ul class="contact__list">
        <li class="contact__item">
          <svg class="contact__icon" viewBox="0 0 14 14" aria-hidden="true"><circle cx="7" cy="7" r="6" fill="none" stroke="#c8262b" stroke-width="1.4"/><path d="M4 7.5 7 4.5 10 7.5V10H4Z" fill="#c8262b"/></svg>
          <span>482 Linden Avenue</span>
        </li>
        <li class="contact__item">
          <svg class="contact__icon" viewBox="0 0 14 14" aria-hidden="true"><circle cx="7" cy="7" r="6" fill="none" stroke="#c8262b" stroke-width="1.4"/><path d="M7 3.5a2.3 2.3 0 0 1 2.3 2.3C9.3 7.6 7 10.5 7 10.5S4.7 7.6 4.7 5.8A2.3 2.3 0 0 1 7 3.5Z" fill="#c8262b"/></svg>
          <span>Maple Grove</span>
        </li>
        <li class="contact__item">
          <svg class="contact__icon" viewBox="0 0 14 14" aria-hidden="true"><circle cx="7" cy="7" r="6" fill="none" stroke="#c8262b" stroke-width="1.4"/><path d="M7 3.5a2.3 2.3 0 0 1 2.3 2.3C9.3 7.6 7 10.5 7 10.5S4.7 7.6 4.7 5.8A2.3 2.3 0 0 1 7 3.5Z" fill="#c8262b"/></svg>
          <span>Minnesota</span>
        </li>
        <li class="contact__item">
          <svg class="contact__icon" viewBox="0 0 14 14" aria-hidden="true"><circle cx="7" cy="7" r="6" fill="none" stroke="#c8262b" stroke-width="1.4"/><rect x="4.5" y="4.5" width="5" height="5" fill="#c8262b"/></svg>
          <span>55369</span>
        </li>
        <li class="contact__item">
          <svg class="contact__icon" viewBox="0 0 14 14" aria-hidden="true"><circle cx="7" cy="7" r="6" fill="none" stroke="#c8262b" stroke-width="1.4"/><rect x="3.8" y="4.8" width="6.4" height="4.4" fill="none" stroke="#c8262b" stroke-width="1.1"/><path d="M3.8 4.8 7 7.4 10.2 4.8" fill="none" stroke="#c8262b" stroke-width="1.1"/></svg>
          <span>dana@mgyguild.org</span>
        </li>
        <li class="contact__item">
          <svg class="contact__icon" viewBox="0 0 14 14" aria-hidden="true"><circle cx="7" cy="7" r="6" fill="none" stroke="#c8262b" stroke-width="1.4"/><path d="M5 3.8 6.3 5.4 5.6 6.3a4.5 4.5 0 0 0 2.1 2.1l.9-.7 1.6 1.3-.8 1.2C7 10.2 3.8 7 3.8 4.6Z" fill="#c8262b"/></svg>
          <span>612 555 0148</span>
        </li>
        <li class="contact__item">
          <svg class="contact__icon" viewBox="0 0 14 14" aria-hidden="true"><circle cx="7" cy="7" r="6" fill="none" stroke="#c8262b" stroke-width="1.4"/><circle cx="7" cy="7" r="3" fill="none" stroke="#c8262b" stroke-width="1.1"/><path d="M4 7H10M7 4V10" stroke="#c8262b" stroke-width="1"/></svg>
          <span>mgyguild.org</span>
        </li>
      </ul>
    </div>
    <div class="contact__rule"></div>

    <div class="brand">
      <span class="brand__dot"></span>
      <span class="brand__name">Maple Grove Youngsters Guild</span>
    </div>
  </section>

  <section class="card card--back" aria-label="Business card, brand side">
    <div class="wash" role="img" aria-label="Soft watercolour washes in blue, green and red"></div>
    <div class="brand">
      <span class="brand__dot"></span>
      <span class="brand__name">Maple Grove Youngsters Guild</span>
    </div>
  </section>

</main>
</body>
</html>
```